Media Services Start-up -- Corporate Website and Logo Design. Inspiration required!

We need a logo design and corporate website design, including coding, for our start-up business.
Vennatra’s value proposition is based on bringing together media content from a vast number of geographies globally, adding human and AI curation, translation and editing, and delivering the content using tailored customer interfaces. On the one hand, the business brings together media coverage from all over the world, and on the other it brings together content, human skills and technology to deliver a supreme customer experience.
Vennatra is a B2B media monitoring and analytics business with emphasis on global customers. Vennatra's service offering is centred around sourcing media content from different markets, processing, storing and delivering the content and insights derived from it using an online platform / mobile app.
The messaging we want to create through the logo is:
- Global scope
- Speed of delivery
- Cost-efficiency
- Multi-lingual
- Tailor-made
- Trustworthy
Target Market(s)
Business to business, PR / Communications, Media, Marketing
Logo Text
Vennatra
Coding
Coded - Design and coding required
Number of Pages Required
5+ page
Font styles to use
Other font styles liked:
- See Design Brief for details
Colors
Designer to choose colors to be used in the design.

```html
<!DOCTYPE html>
<html lang="en">
<head>
<meta charset="utf-8">
<title>Vennatra — Website Screens</title>
<link rel="stylesheet" href="https://fonts.googleapis.com/css2?family=Arimo:ital,wght@0,400;0,700;1,400&family=Roboto:wght@400;500;700&display=swap">
<style>
  :root {
    --backdrop: #6bdcef;
    --navy: #0c1a4a;
    --navy-deep: #0a1547;
    --orange: #ff9505;
    --white: #ffffff;
    --card: #f6f6f8;
    --ink: #111111;
    --footer: #000000;
    --footer-bar: #141414;
    --faint-logo: #0f1c4d;
    --sans: "Arimo", Arial, sans-serif;
    --ui: "Roboto", Arial, sans-serif;
  }
  * { box-sizing: border-box; margin: 0; padding: 0; }
  html, body { width: 773px; height: 1200px; overflow: hidden; }
  body { background: var(--backdrop); font-family: var(--sans); position: relative; }

  .screen { position: absolute; left: 61px; width: 649px; overflow: hidden; }
  .screen--home { top: 76px; height: 351px; }
  .screen--solutions { top: 474px; height: 651px; }

  .topbar { position: absolute; left: 0; top: 0; width: 100%; height: 51px; }
  .topbar--navy { background: var(--navy-deep); }
  .topbar--orange { background: var(--orange); }
  .brand { position: absolute; left: 54px; top: 14px; font-weight: 700; font-size: 17px; letter-spacing: 0.3px; }
  .topbar--navy .brand { color: var(--orange); }
  .topbar--orange .brand { color: var(--navy); }
  .menu { position: absolute; left: 236px; top: 19px; display: flex; gap: 16px; list-style: none; }
  .menu li { color: var(--white); font-weight: 700; font-size: 9.5px; letter-spacing: 0.1px; white-space: nowrap; }

  .hero-photo { position: absolute; left: 0; top: 51px; width: 100%; height: 300px;
    background: linear-gradient(110deg, #1d2a3a 0%, #3a3a44 30%, #24324c 55%, #5a4630 80%, #8a6a3c 100%); }
  .hero-caption { position: absolute; left: 53px; top: 173px; width: 289px; height: 88px;
    background: rgba(40, 40, 40, 0.55); color: var(--white); }
  .hero-caption h1 { position: absolute; left: 10px; top: 13px; font-size: 13.6px; font-weight: 700;
    letter-spacing: 0.2px; white-space: nowrap; }
  .hero-caption p { position: absolute; left: 10px; top: 32px; width: 320px; text-align: center;
    font-size: 10.3px; line-height: 14px; white-space: nowrap; }

  .lead-form { position: absolute; left: 441px; top: 113px; width: 155px; height: 176px; background: var(--white); }
  .lead-form h2 { font-family: var(--ui); font-weight: 400; font-size: 11px; color: var(--navy); text-align: center; margin-top: 20px; line-height: 14px; }
  .lead-form h2 strong { font-weight: 700; }
  .field { position: absolute; left: 13px; width: 129px; height: 21px; border: 1px solid #d8d8d8;
    font-family: var(--ui); font-size: 8px; color: var(--ink); padding: 5px 5px; }
  .field--name { top: 58px; } .field--email { top: 81px; } .field--phone { top: 104px; }
  .cta { position: absolute; left: 13px; top: 129px; width: 129px; height: 20px; background: var(--orange);
    color: var(--white); font-family: var(--ui); font-weight: 700; font-size: 8px; text-align: center; line-height: 20px; letter-spacing: 0.3px; }

  .solutions-photo { position: absolute; left: 0; top: 51px; width: 100%; height: 414px;
    background: linear-gradient(125deg, #7a3418 0%, #b5552a 30%, #c9692e 50%, #a8502a 70%, #8c4a2a 100%); }
  .solutions-title { position: absolute; left: 0; width: 100%; top: 79px; text-align: center;
    color: var(--white); font-weight: 700; font-size: 16.5px; letter-spacing: 0.4px; }

  .service { position: absolute; background: var(--card); width: 172px; height: 134px; text-align: center; }
  .service h3 { font-weight: 700; font-size: 10px; color: var(--ink); margin-top: 12px; line-height: 10.5px; letter-spacing: 0.3px; white-space: nowrap; }
  .service p { font-style: italic; font-size: 5.6px; line-height: 12.8px; color: var(--ink); text-align: justify; margin: 7px 11px 0; }
  .service .more { position: absolute; left: 54px; bottom: 11px; width: 64px; height: 13px; background: var(--navy);
    color: var(--white); font-size: 7.3px; line-height: 13px; }
  .s1 { left: 53px; top: 126px; }
  .s2 { left: 238px; top: 126px; }
  .s3 { left: 424px; top: 126px; }
  .s4 { left: 143px; top: 288px; width: 173px; height: 136px; }
  .s5 { left: 336px; top: 288px; width: 173px; height: 136px; }
  .s4 .more, .s5 .more { left: 55px; }
  .s4 h3 { margin-top: 8px; }
  .s5 h3 { margin-top: 13px; }

  .site-footer { position: absolute; left: 0; top: 465px; width: 100%; height: 167px; background: var(--footer); color: var(--white); }
  .footer-brand { position: absolute; left: 83px; top: 75px; color: var(--faint-logo); font-size: 17px; }
  .footer-rule { position: absolute; left: 188px; top: 66px; width: 1px; height: 40px; background: #cfcfcf; }
  .footer-tagline { position: absolute; left: 198px; top: 74px; font-size: 8.3px; line-height: 14px; }
  .contact { position: absolute; display: flex; align-items: flex-start; gap: 10px; }
  .contact svg { flex: none; }
  .contact--phone { left: 393px; top: 42px; font-weight: 700; font-size: 10.2px; line-height: 14px; }
  .contact--place { left: 398px; top: 87px; font-size: 8.3px; line-height: 14px; }
  .contact--mail { left: 400px; top: 135px; font-size: 8.3px; }
  .copyright-bar { position: absolute; left: 0; top: 632px; width: 100%; height: 19px; background: var(--footer-bar);
    color: var(--white); font-size: 8px; text-align: center; line-height: 19px; }
</style>
</head>
<body>

<section class="screen screen--home">
  <header class="topbar topbar--navy">
    <div class="brand">VENNATRA</div>
    <ul class="menu"><li>HOME</li><li>SOLUTION</li><li>HOW WE DO IT</li><li>OUR PEOPLE</li><li>OUR TECHNOLOGY</li></ul>
  </header>
  <div class="hero-photo" role="img" aria-label="Photo of a woman working at a desktop monitor in a dim office"></div>
  <div class="hero-caption">
    <h1>DELIVERING GLOBAL MEDIA INTELLIGENCE</h1>
    <p>Vennatra is an international media intelligence service provider.<br>We help communications teams build and operate truly global<br>media monitoring and measurement programmes.</p>
  </div>
  <form class="lead-form">
    <h2>Learn More About<br><strong>Vennatra</strong></h2>
    <div class="field field--name">Name</div>
    <div class="field field--email">Email</div>
    <div class="field field--phone">Phone</div>
    <div class="cta">GET STARTED</div>
  </form>
</section>

<section class="screen screen--solutions">
  <header class="topbar topbar--orange">
    <div class="brand">VENNATRA</div>
    <ul class="menu"><li>HOME</li><li>SOLUTION</li><li>HOW WE DO IT</li><li>OUR PEOPLE</li><li>OUR TECHNOLOGY</li></ul>
  </header>
  <div class="solutions-photo" role="img" aria-label="Orange-toned photo of hands on a laptop with glowing data overlay"></div>
  <h2 class="solutions-title">SOLUTIONS</h2>

  <article class="service s1">
    <h3>CONTENT SOURCING</h3>
    <p>Identify geographies and markets of interest. Build target media source lists to monitoring and measurement requirements. Using our transparent cost calculator, we help you with accurate budgeting and choices to ensure you meet your strategy</p>
    <div class="more">READ MORE</div>
  </article>
  <article class="service s2">
    <h3>CONTENT COLLECTION</h3>
    <p>We consolidate and manage the delivery of your global media content into a Cloud-based scalable media platform, taking the headache of content management away from your teams.</p>
    <div class="more">READ MORE</div>
  </article>
  <article class="service s3">
    <h3>CONTENT AUGMENTATION</h3>
    <p>We manage and normalise all of the source-level reference data - country, language, reach etc. We add editorial validation to ensure only the content required reaches your delivery, removing inevitable noise from source providers</p>
    <div class="more">READ MORE</div>
  </article>
  <article class="service s4">
    <h3>MEDIA INSIGHTS<br>&amp;<br>CONSULTANCY</h3>
    <p>Levering the normalised content sets from your integrated monitoring service, we can analyse and tag your coverage based on complex qualitative measurement criteria,</p>
    <div class="more">READ MORE</div>
  </article>
  <article class="service s5">
    <h3>CONTENT DELIVERY</h3>
    <p>Early morning delivery of a consolidated, Customised email templates, delivering content in templates Customised platform - modern portal tailored to meet your media management needs, removing the unwanted clutter and focusing on the job at hand</p>
    <div class="more">READ MORE</div>
  </article>

  <footer class="site-footer">
    <div class="footer-brand">VENNATRA</div>
    <div class="footer-rule"></div>
    <p class="footer-tagline">Comprehensive Print, Online, TV,<br>Radio &amp; Social media in realtime</p>
    <div class="contact contact--phone">
      <svg width="16" height="16" viewBox="0 0 24 24" fill="none" stroke="#fff" stroke-width="1.4"><path d="M5 3h4l2 5-2.5 1.5a11 11 0 0 0 6 6L16 13l5 2v4a2 2 0 0 1-2 2A17 17 0 0 1 3 5a2 2 0 0 1 2-2z"/><path d="M15 3a6 6 0 0 1 6 6M15 6.5a3 3 0 0 1 2.5 2.5"/></svg>
      <span>(02) 5550 0148 or<br>1300 555 016</span>
    </div>
    <div class="contact contact--place">
      <svg width="9" height="12" viewBox="0 0 18 24"><path fill="#fff" d="M9 0a9 9 0 0 0-9 9c0 6.5 9 15 9 15s9-8.5 9-15a9 9 0 0 0-9-9zm0 12.5A3.5 3.5 0 1 1 9 5.5a3.5 3.5 0 0 1 0 7z"/></svg>
      <span>Level 2, 118 Harbour Lane, Northgate,<br>NSW 2099 Australia</span>
    </div>
    <div class="contact contact--mail">
      <svg width="12" height="9" viewBox="0 0 24 18" fill="none" stroke="#fff" stroke-width="1.6"><rect x="1" y="1" width="22" height="16"/><path d="M1 1l11 9 11-9M1 17l8-7M23 17l-8-7"/></svg>
      <span>team@vennatra.com</span>
    </div>
  </footer>
  <div class="copyright-bar">Copyrights © 2019 All Rights Reserved</div>
</section>

</body>
</html>
```